my website is tavorinque.com. (brand name is ta belle vitrine) This is just a template that i have choose for. The content and the pictures are not about my business just the template.
I would like to have 4 pages for now. 1 homepage, which will be an overview for all pages, it is right now in this way. It will directly highlight my story. My website will tell an exclusive story about details which makes the difference and will make people happy with very small things. It will be art related but very stylish as well. I also want to have a event agenda on my homepage where people can see where my next event is. Page 2 my blog, where I will write weekly about mindset, lifestyle and details. Inspiration place for people who are looking for unique and exclusive approaches in life. Page 3 shop, where I will sell my stuff which is handmade and unique, it will be limited edition stuff. Mostly I will make the designs from marbling art, which I am a teacher for. (https://www.vidoranta.com/watch?v=KpwuzRaxTmo) check this video out for more. Page 4 is book page. Here people will be able to book private or group classes for marbling art (check the video). I have already a community of more than 500 people on gath rix, which will be my public as well. I wanna implement the gath rix button on this page as well. to be able to track.

This is about my website. I also need a logo for my brand, which will suit my website and my goals.

I can also give you a reference website, which really like as structure and style;
https://www.brightorvalco.com/products/the-morning-ledger?gclid=Xr4TpLmwq2HsVD9KEBsZTrc-WkPhyQ-uvlEjdRs3NKaOYFCBWMpuTzG8xyCVbhdnLWRqoaNf_2e8ZtpRvHbAwq9FLQ_hqgQ

Logo Text

ta belle vitrine

Coding

Coded - Design and coding required

Number of Pages Required

4 page

Requirements
Must have
• I can also give you a reference website, which really like as structure and style;
• https://www.brightorvalco.com/products/the-morning-ledger?gclid=Xr4TpLmwq2HsVD9KEBsZTrc-WkPhyQ-uvlEjdRs3NKaOYFCBWMpuTzG8xyCVbhdnLWRqoaNf_2e8ZtpRvHbAwq9FLQ_hqgQ

```html
<!DOCTYPE html>
<html lang="en">
<head>
<meta charset="utf-8">
<title>ta belle vitrine — Home</title>
<link rel="stylesheet" href="https://fonts.googleapis.com/css2?family=Montserrat:wght@400;500;600&family=Lato:wght@300;400&family=Libre+Baskerville:ital@1&display=swap">
<style>
  :root {
    --ink: #111111;
    --nav: #555555;
    --white: #ffffff;
    --band: #000000;
    --muted: #8a8a8a;
    --body: #5a5a5a;
    --hero-a: #3a3634;
    --hero-b: #1f1d1c;
    --marble-a: #a9797a;
    --marble-b: #6e4e4b;
    --strip-a: #4a1e1e;
    --strip-b: #2a1a18;
  }
  * { box-sizing: border-box; margin: 0; padding: 0; }
  html, body { width: 1200px; height: 1200px; overflow: hidden; background: var(--white); }
  body { position: relative; font-family: "Montserrat", sans-serif; color: var(--ink); }

  .site-header { position: absolute; left: 0; top: 0; width: 1200px; height: 75px; background: var(--white); }
  .brand { position: absolute; left: 155px; top: 24px; display: flex; align-items: center; gap: 10px; }
  .brand-dot { width: 26px; height: 26px; border: 1.5px solid var(--ink); border-radius: 50%; }
  .brand-name { font-family: "Montserrat", sans-serif; font-size: 14px; font-weight: 500; color: var(--ink); }
  .main-nav { position: absolute; top: 27px; left: 475px; display: flex; gap: 57px; }
  .main-nav a { font-size: 12.5px; color: var(--nav); text-decoration: none; letter-spacing: 0.3px; }
  .menu-toggle { position: absolute; left: 1003px; top: 27px; }

  .hero { position: absolute; left: 0; top: 75px; width: 1200px; height: 525px;
    background: radial-gradient(ellipse at 50% 20%, #5a5048 0%, var(--hero-a) 45%, var(--hero-b) 100%);
    color: var(--white); text-align: center; }
  .hero-kicker { position: absolute; top: 206px; width: 100%; font-size: 12px; font-weight: 600; letter-spacing: 0.3px; }
  .hero-rule { position: absolute; top: 253px; left: 570px; width: 60px; height: 1px; background: var(--white); }
  .hero-title { position: absolute; top: 278px; width: 100%; font-size: 34px; font-weight: 500; line-height: 53px; letter-spacing: 0.5px; }
  .hero-cta { position: absolute; left: 513px; top: 403px; width: 174px; height: 47px; border: 2px solid var(--white);
    display: flex; align-items: center; justify-content: center; font-size: 10px; font-weight: 500; }

  .promo-band { position: absolute; left: 0; top: 600px; width: 1200px; height: 120px; background: var(--band); color: var(--white); }
  .promo-text { position: absolute; left: 326px; top: 52px; font-size: 10px; font-weight: 600; letter-spacing: 1.6px; }
  .promo-cta { position: absolute; left: 738px; top: 39px; width: 151px; height: 42px; border-radius: 21px; background: var(--white);
    color: var(--ink); display: flex; align-items: center; justify-content: center; font-size: 10px; font-weight: 500; }

  .story { position: absolute; left: 0; top: 720px; width: 1200px; height: 427px; background: var(--white); }
  .story-title { position: absolute; left: 163px; top: 56px; font-size: 17px; font-weight: 500; letter-spacing: 0.3px; }
  .story-sub { position: absolute; left: 162px; top: 86px; font-family: "Lato", sans-serif; font-size: 10px; color: var(--muted); letter-spacing: 1px; }
  .story-rule { position: absolute; left: 161px; top: 112px; width: 22px; height: 1px; background: var(--ink); }
  .story-copy { position: absolute; left: 162px; top: 145px; width: 380px; font-family: "Lato", sans-serif; font-size: 10.4px;
    line-height: 18.8px; color: var(--body); letter-spacing: 0.6px; }
  .story-copy p + p { margin-top: 18.8px; }
  .story-cta { position: absolute; left: 161px; top: 330px; width: 147px; height: 38px; border: 1px solid var(--ink);
    display: flex; align-items: center; justify-content: center; font-size: 9.5px; font-weight: 500; }
  .story-media { position: absolute; left: 577px; top: 0; width: 473px; height: 427px;
    background: linear-gradient(135deg, var(--marble-a) 0%, #946563 50%, var(--marble-b) 100%); }

  .gallery-strip { position: absolute; left: 0; top: 1147px; width: 1200px; height: 53px;
    background: linear-gradient(90deg, var(--strip-a), var(--strip-b) 60%, #3b2a24); }
</style>
</head>
<body>
  <header class="site-header">
    <div class="brand"><span class="brand-dot"></span><span class="brand-name">ta belle vitrine</span></div>
    <nav class="main-nav">
      <a href="#">HOME</a><a href="#">BLOG</a><a href="#">SHOP</a><a href="#">BOOK</a>
    </nav>
    <svg class="menu-toggle" width="22" height="17" viewBox="0 0 22 17" aria-label="Menu">
      <rect x="0" y="1" width="22" height="2" fill="#111"/>
      <rect x="0" y="7.5" width="22" height="2" fill="#111"/>
      <rect x="0" y="14" width="22" height="2" fill="#111"/>
    </svg>
  </header>

  <section class="hero" role="img" aria-label="Marbling tray with floating paint patterns surrounded by jars of colour and brushes">
    <p class="hero-kicker">ELEGANT BEAUTY IN AN ART FORM</p>
    <span class="hero-rule"></span>
    <h1 class="hero-title">AN UNPARALLELED SELECTION<br>NEW ARRIVALS ARE HERE</h1>
    <a class="hero-cta">CLICK TO SHOP NOW</a>
  </section>

  <section class="promo-band">
    <p class="promo-text">BEST ONLINE EBRU ART STORE NEAR YOU, SHOP NOW</p>
    <a class="promo-cta">SHOP NOW</a>
  </section>

  <section class="story">
    <h2 class="story-title">OUR BEGINNING</h2>
    <p class="story-sub">CLOSER TO THE STARS</p>
    <span class="story-rule"></span>
    <div class="story-copy">
      <p>Donec rutrum congue leo eget malesuada. Curabitur non nulla sit amet nisl tempus convallis quis ac lectus. Sed porttitor lectus nibh. Proin eget tortor risus. Nulla porttitor accumsan tincidunt. Nulla porttitor accumsan tincidunt.</p>
      <p>Curabitur aliquet quam id dui posuere blandit.<br>Nulla quis lorem ut libero malesuada feugiat. Donec rutrum congue leo eget malesuada. Curabitur aliquet quam id dui posuere blandit.</p>
    </div>
    <a class="story-cta">SEE PORTFOLIO</a>
    <div class="story-media" role="img" aria-label="Hand drawing a stylus through pink marbled paint on water"></div>
  </section>

  <div class="gallery-strip" role="img" aria-label="Paint jars and brushes on a studio table"></div>
</body>
</html>
```